Financial Advisor Resource Firm needs business card design

Need business card design for company in Omaha NE called Meridale Circle. We provide resources to financial advisors....workshop programs, retirement analysis, and insurance planning. I would like to see designs that use grays, greens, black, and white colors. The final design should communicate 'collaboration' and be simple yet attractive to financial planning clients. I will attached our logo and another picture of a puzzle piece coming together. I would like the incorporate the puzzle picture somehow, maybe on the back somehow, with color or just the gray scale....OR, the picture be the front of the card with 'Meridale' definition on it (see upload) and then company logo, employee name, title, address on the back (see ppt uploaded). The following disclosure needs to be included somewhere- Advisory services offered through Stonebrook Assets, LLC.
Updates

I uploaded a svg and ai file of the logo

Target Market(s)

Financial planning clients and financial advisors....so pretty diverse age range of about 40-70.

Industry/Entity Type

Financial Planning

Contact Information for Business Card

Tobias L. Fenwright, MBA
Founder/President
5287 E. Larkin Road
Suite 230
Omaha, NE 68190
Phone- (402) 555-0147
Cell- (402) 555-0183
Fax- (402) 555-0129
email- tobias@meridaleplan.example
web address- www.meridaleplan.example

Colors
1b1b1b
474747
d3d3d3
ffffff
9bcb3c
abd036

Requirements
Must have
• Must include logo provided, must be 2 sided, and must have disclosure...all of these items listed in project description

```html
<!DOCTYPE html>
<html lang="en">
<head>
<meta charset="utf-8">
<title>Meridale Circle – Business Card</title>
<link rel="stylesheet" href="https://fonts.googleapis.com/css2?family=Lato:wght@400;700&family=Roboto+Condensed:wght@400&display=swap">
<style>
  :root {
    --ink: #1b1b1b;
    --graphite: #474747;
    --mist: #d3d3d3;
    --paper: #ffffff;
    --leaf: #9bcb3c;
    --lime: #abd036;
    --backdrop: #e6e6e4;
    --card-light: #f4f4f3;
    --muted-text: #8a8a8a;
  }
  * { margin: 0; padding: 0; box-sizing: border-box; }
  html, body {
    width: 1200px; height: 900px; overflow: hidden;
    background: var(--backdrop);
  }
  .stage {
    position: relative; width: 1200px; height: 900px;
    display: flex; align-items: center; justify-content: center;
  }
  .card {
    position: relative; width: 1050px; height: 600px;
    background: linear-gradient(100deg, var(--paper) 40%, var(--card-light) 100%);
    box-shadow: 0 10px 30px rgba(0,0,0,0.18);
    overflow: hidden;
    font-family: "Lato", Arial, sans-serif;
  }
  .card__panel { position: absolute; inset: 0; width: 100%; height: 100%; }
  .panel-dark { fill: var(--ink); }
  .panel-edge { fill: none; stroke: var(--leaf); stroke-width: 7; }

  .contact {
    position: absolute; left: 48px; top: 212px; color: var(--muted-text);
  }
  .contact__name {
    font-weight: 700; font-size: 32px; color: var(--leaf);
    text-transform: uppercase; letter-spacing: 0.2px; line-height: 1;
  }
  .contact__credential { font-weight: 400; font-size: 27px; }
  .contact__title { font-size: 27px; margin-top: 6px; line-height: 1.1; }
  .contact__list { list-style: none; margin-top: 22px; }
  .contact__item {
    display: flex; align-items: center; gap: 10px;
    font-size: 27px; line-height: 33.5px;
  }
  .contact__icon { width: 20px; height: 20px; fill: var(--leaf); flex: none; }
  .contact__address { font-size: 27px; line-height: 34px; margin-top: 14px; }

  .brand {
    position: absolute; left: 488px; top: 88px; width: 520px;
    text-align: center;
  }
  .brand__lockup {
    display: inline-flex; align-items: center; gap: 14px;
  }
  .brand__dot {
    width: 30px; height: 30px; border-radius: 50%; background: var(--leaf);
  }
  .brand__name {
    font-weight: 700; font-size: 46px; letter-spacing: 2px;
    color: var(--ink); text-transform: uppercase; line-height: 1;
  }
  .brand__disclosure {
    margin-top: 48px;
    font-family: "Roboto Condensed", "Arial Narrow", sans-serif;
    font-size: 21px; line-height: 31px; color: var(--ink);
    text-transform: uppercase;
  }
</style>
</head>
<body>
<main class="stage">
  <article class="card">
    <svg class="card__panel" viewBox="0 0 1050 600" aria-hidden="true">
      <path class="panel-dark" d="M0 0 H205 C430 55 620 300 630 600 H0 Z"/>
      <path class="panel-edge" d="M205 0 C437 55 630 300 640 600"/>
    </svg>

    <section class="contact">
      <h1 class="contact__name">Tobias L. Fenwright, <span class="contact__credential">MBA</span></h1>
      <p class="contact__title">Founder/President</p>
      <ul class="contact__list">
        <li class="contact__item">
          <svg class="contact__icon" viewBox="0 0 20 20"><path d="M2 7c0-3 3-4 8-4s8 1 8 4l-3 1-1-2H6L5 8zM5 9h10l2 8H3z"/></svg>
          (402) 555-0147
        </li>
        <li class="contact__item">
          <svg class="contact__icon" viewBox="0 0 20 20"><path d="M6 1h8a1 1 0 011 1v16a1 1 0 01-1 1H6a1 1 0 01-1-1V2a1 1 0 011-1zm1 2v11h6V3zm3 12.5a1 1 0 100 2 1 1 0 000-2z"/></svg>
          (402) 555-0183
        </li>
        <li class="contact__item">
          <svg class="contact__icon" viewBox="0 0 20 20"><path d="M5 1h10v5H5zM2 7h16v8h-3v4H5v-4H2zm5 6v4h6v-4z"/></svg>
          (402) 555-0129
        </li>
        <li class="contact__item">
          <svg class="contact__icon" viewBox="0 0 20 20"><path d="M1 4h18v12H1zm2 2v1l7 5 7-5V6l-7 5z"/></svg>
          tobias@meridaleplan.example
        </li>
        <li class="contact__item">
          <svg class="contact__icon" viewBox="0 0 20 20"><path d="M10 1a9 9 0 110 18 9 9 0 010-18zm-2 4l-3 2 1 3 3 1 1 4 2-1v-3l3-2-1-2-3 1z"/></svg>
          www.meridaleplan.example
        </li>
      </ul>
      <address class="contact__address">5287 E. Larkin Road<br>Suite 230 Omaha, NE 68190</address>
    </section>

    <section class="brand">
      <div class="brand__lockup">
        <span class="brand__dot"></span>
        <span class="brand__name">Meridale Circle</span>
      </div>
      <p class="brand__disclosure">Advisory services offered through<br>Stonebrook Assets, LLC.</p>
    </section>
  </article>
</main>
</body>
</html>
```